limo company looking for a graphic business card with professional look and feel

Looking for a business card design that can give you the full picture of the limo company by looking at the card - we provide airport service, wedding, birthday, night out, etc... we have sedans, suvs , limos, and party buses. I want the business card to have a professional look because we are targetting corporate clients as well as regular retail.
Info about the business can be found at: http://brevlink.example/Qm4Tz7
Target Market(s)
corporate clients and retail
Industry/Entity Type
Business
Contact Information for Business Card
I would like the logo and the name of the company to be in raised print - not sure if design makes a difference for that or just print - I need it designed in 350dpi
Requirements
Must have
- pictures of vehicle types (sedans, suvs, limos, party bus). pictures of interior of the limos if possible. list service types (weddings, birthdays, proms, airport transportation) & service areas (houston, the woodlands, spring, tomball, cypress, kingwood).
Nice to have
- nice professional look to it.

```html
<!DOCTYPE html>
<html lang="en">
<head>
<meta charset="utf-8">
<title>Meridian Livery &amp; Transportation – Business Card</title>
<link rel="stylesheet" href="https://fonts.googleapis.com/css2?family=Open+Sans:wght@400;600;700&display=swap">
<style>
  :root {
    --page: #e9e6e1;
    --card: #050505;
    --band: #3a3a3c;
    --band-edge: #1b1b1c;
    --ink: #f4f4f4;
    --ink-soft: #cfcfcf;
    --rule: #8a8a8a;
  }
  * { box-sizing: border-box; margin: 0; padding: 0; }
  html, body {
    width: 1200px; height: 780px; overflow: hidden;
    background: var(--page);
    font-family: "Open Sans", Arial, sans-serif;
    color: var(--ink);
  }
  .sheet {
    width: 1200px; height: 780px;
    display: flex; flex-direction: column; align-items: center; justify-content: center;
    gap: 34px;
  }
  .card {
    width: 620px; height: 354px;
    background: var(--card);
    position: relative; overflow: hidden;
    box-shadow: 0 6px 18px rgba(0,0,0,.25);
  }

  /* front */
  .front-top { position: absolute; left: 0; top: 0; width: 100%; height: 150px; }
  .brand {
    position: absolute; left: 34px; top: 52px;
    display: flex; align-items: center; gap: 12px;
  }
  .brand-dot { width: 12px; height: 12px; border-radius: 50%; background: var(--ink); }
  .brand-name {
    font-weight: 600; font-size: 22px; line-height: 1.2; color: var(--ink);
  }
  .contact-person {
    position: absolute; right: 30px; top: 26px; text-align: left;
  }
  .person-name { font-size: 27px; font-weight: 600; line-height: 1.05; }
  .person-title { font-size: 16px; color: var(--ink-soft); }
  .person-phone {
    margin-top: 8px; font-size: 17px; display: flex; align-items: center; gap: 10px; color: var(--ink-soft);
  }
  .icon-tile {
    width: 18px; height: 18px; background: var(--ink); border-radius: 2px;
    display: inline-flex; align-items: center; justify-content: center;
  }
  .photo-strip {
    position: absolute; left: 0; top: 150px; width: 100%; height: 138px;
    display: grid; grid-template-columns: repeat(4, 1fr); gap: 4px;
    border-top: 4px solid #2b2b2b;
  }
  .photo { height: 100%; }
  .photo--green { background: radial-gradient(circle at 50% 40%, #5fd08a, #0d6b34 60%, #063418); }
  .photo--blue { background: radial-gradient(circle at 50% 35%, #5d7bd6, #1c2a66 55%, #070b20); }
  .photo--suv { background: linear-gradient(180deg, #b9c3cf 0%, #8d95a0 45%, #2a2d33 70%, #9aa0a6 100%); }
  .photo--purple { background: radial-gradient(circle at 55% 65%, #8c3cc8, #2a2e3a 55%, #0b0c10); }
  .info-band {
    position: absolute; left: 0; bottom: 0; width: 100%; height: 66px;
    background: var(--band); border-top: 4px solid var(--band-edge);
    display: flex; align-items: center; justify-content: space-between;
    padding: 0 30px;
  }
  .info-item { display: flex; align-items: center; gap: 12px; font-size: 18px; color: var(--ink); }

  /* back */
  .back-content {
    position: absolute; inset: 0;
    display: flex; flex-direction: column; align-items: center; padding-top: 36px;
  }
  .back-content .brand { position: static; margin-bottom: 24px; }
  .rule { width: 470px; height: 1px; background: var(--rule); margin: 4px 0; }
  .section-title {
    font-weight: 700; font-size: 19px; letter-spacing: .5px; text-transform: uppercase; margin-top: 6px;
  }
  .section-list { font-size: 16px; color: var(--ink-soft); margin-bottom: 6px; }
</style>
</head>
<body>
<main class="sheet">

  <section class="card card--front">
    <div class="front-top">
      <div class="brand">
        <span class="brand-dot"></span>
        <span class="brand-name">Meridian Livery<br>&amp; Transportation</span>
      </div>
      <div class="contact-person">
        <div class="person-name">Employee Name</div>
        <div class="person-title">Managing Director</div>
        <div class="person-phone">
          123 456 7890
          <span class="icon-tile">
            <svg width="10" height="12" viewBox="0 0 10 12"><rect x="1" y="0.5" width="8" height="11" rx="1.2" fill="none" stroke="#050505" stroke-width="1.3"/><rect x="3.5" y="9" width="3" height="1" fill="#050505"/></svg>
          </span>
        </div>
      </div>
    </div>

    <div class="photo-strip">
      <div class="photo photo--green" role="img" aria-label="Party bus interior lit in green"></div>
      <div class="photo photo--blue" role="img" aria-label="Limousine interior with blue lighting"></div>
      <div class="photo photo--suv" role="img" aria-label="Black SUV limousine parked outside"></div>
      <div class="photo photo--purple" role="img" aria-label="Limousine interior with purple seating"></div>
    </div>

    <div class="info-band">
      <div class="info-item">
        <span class="icon-tile">
          <svg width="12" height="9" viewBox="0 0 12 9"><rect x="0.6" y="0.6" width="10.8" height="7.8" fill="none" stroke="#3a3a3c" stroke-width="1.2"/><path d="M0.6 0.6 L6 5 L11.4 0.6" fill="none" stroke="#3a3a3c" stroke-width="1.2"/></svg>
        </span>
        you@yourmail.example
      </div>
      <div class="info-item">
        <span class="icon-tile">
          <svg width="12" height="12" viewBox="0 0 12 12"><circle cx="6" cy="6" r="5" fill="none" stroke="#3a3a3c" stroke-width="1.1"/><ellipse cx="6" cy="6" rx="2.2" ry="5" fill="none" stroke="#3a3a3c" stroke-width="1"/><line x1="1" y1="6" x2="11" y2="6" stroke="#3a3a3c" stroke-width="1"/></svg>
        </span>
        www.yourweb.example
      </div>
    </div>
  </section>

  <section class="card card--back">
    <div class="back-content">
      <div class="brand">
        <span class="brand-dot"></span>
        <span class="brand-name">Meridian Livery<br>&amp; Transportation</span>
      </div>
      <h2 class="section-title">Service</h2>
      <p class="section-list">weddings | birthdays | proms | airport transportation</p>
      <div class="rule"></div>
      <h2 class="section-title">Service Areas</h2>
      <p class="section-list">houston | the woodlands | spring | tomball | cypress | kingwood</p>
      <div class="rule"></div>
      <h2 class="section-title">Vehicle Types</h2>
      <p class="section-list">sedans | suvs | limos | party bus</p>
    </div>
  </section>

</main>
</body>
</html>
```